Business Cards used to invite people to our church

We are a church and have need of a business card sized advertisement that allows our members to hand them out in order to invite people to the church. I need the front of the card to say "You're Invited" or "Come Check us out". with the service times on the back of the card later.
I have attached one of the OLD cards we have used in the past, but we want a complete makeover, into a more modern style that does not require the image.
I am also replacing the old logo with a newer "flat" logo which is attached.
Please use marketing colors. (blue or red or something that catches attention)
Create a card that DOES NOT have the picture of the two people on the front
The information on the sample card back is correct to go onto new card
Target Market(s)
anyone
Industry/Entity Type
Business
Contact Information for Business Card
sertice times and address information which you can get from the sample card I uploaded. It should have "You're Invited" or "Come Check us out" on the front of the card with out logo.

```html
<!DOCTYPE html>
<html lang="en">
<head>
<meta charset="utf-8">
<title>Grace Harbor Ministries – Invitation Card</title>
<link rel="stylesheet" href="https://fonts.googleapis.com/css2?family=Source+Sans+3:ital,wght@0,600;0,700;1,700&display=swap">
<style>
  :root {
    --stage: #000000;
    --card: #ffffff;
    --red: #ee1111;
    --blush: #fcdede;
    --ink: #111111;
  }
  * { margin: 0; padding: 0; box-sizing: border-box; }
  html, body { width: 1200px; height: 900px; overflow: hidden; background: var(--stage); }
  body { position: relative; font-family: "Source Sans 3", Arial, sans-serif; }

  .card {
    position: absolute;
    top: 275px;
    width: 477px;
    height: 294px;
    background: var(--card);
    overflow: hidden;
  }
  .card--front { left: 116px; border-radius: 0 50px 0 50px; }
  .card--back  { left: 622px; border-radius: 50px 0 50px 0; }

  .front-accent {
    position: absolute;
    left: 38px; top: 10px;
    width: 412px; height: 276px;
    background: var(--blush);
    border-radius: 70px 70px 120px 120px;
  }
  .invite-word {
    position: absolute;
    font-style: italic;
    font-weight: 700;
    font-size: 39px;
    line-height: 1;
    color: var(--red);
    letter-spacing: 0.5px;
  }
  .invite-word--come  { left: 33px;  top: 55px; }
  .invite-word--check { left: 149px; top: 105px; }
  .invite-word--us    { left: 294px; top: 155px; }
  .invite-word--out   { left: 357px; top: 205px; }

  .contact {
    position: absolute;
    left: 0; right: 0;
    text-align: center;
    font-weight: 600;
    font-size: 13px;
    color: var(--ink);
  }
  .contact--phone   { top: 23px; }
  .contact--address { top: 44px; }
  .contact svg { width: 10px; height: 10px; vertical-align: -1px; margin-right: 3px; fill: var(--red); }

  .ministry-name {
    position: absolute;
    left: 0; right: 0; top: 78px;
    display: flex; align-items: center; justify-content: center; gap: 10px;
  }
  .ministry-name__dot { width: 18px; height: 18px; border-radius: 50%; background: var(--red); }
  .ministry-name__text {
    font-weight: 700;
    font-size: 30px;
    line-height: 1.05;
    color: var(--red);
    text-align: center;
  }

  .schedule {
    position: absolute;
    left: 115px; width: 250px; top: 205px;
    list-style: none;
  }
  .schedule__row {
    display: flex; align-items: baseline;
    font-weight: 700; font-size: 13px; color: var(--red);
    height: 24.5px;
  }
  .schedule__leader {
    flex: 1; margin: 0 2px;
    border-bottom: 2px dotted var(--red);
    transform: translateY(-3px);
  }
</style>
</head>
<body>
  <section class="card card--front" aria-label="Card front">
    <div class="front-accent"></div>
    <span class="invite-word invite-word--come">COME</span>
    <span class="invite-word invite-word--check">CHECK</span>
    <span class="invite-word invite-word--us">US</span>
    <span class="invite-word invite-word--out">OUT</span>
  </section>

  <section class="card card--back" aria-label="Card back">
    <p class="contact contact--phone">
      <svg viewBox="0 0 10 10" aria-hidden="true"><path d="M1 3c0-1 1-2 4-2s4 1 4 2v1H7V3H3v1H1zM2 5h6l1 4H1z"/></svg>1-800-555-0142
    </p>
    <p class="contact contact--address">
      <svg viewBox="0 0 10 10" aria-hidden="true"><path d="M5 0a3.4 3.4 0 0 0-3.4 3.4C1.6 6 5 10 5 10s3.4-4 3.4-6.6A3.4 3.4 0 0 0 5 0zm0 4.7a1.3 1.3 0 1 1 0-2.6 1.3 1.3 0 0 1 0 2.6z"/></svg>2480. Cedar Lane - Oakridge, Tx 75990
    </p>

    <div class="ministry-name">
      <span class="ministry-name__dot"></span>
      <span class="ministry-name__text">Grace Harbor<br>Ministries</span>
    </div>

    <ul class="schedule">
      <li class="schedule__row"><span>Sunday</span><span class="schedule__leader"></span><span>9:00 Am</span></li>
      <li class="schedule__row"><span>Sunday</span><span class="schedule__leader"></span><span>11.00 Am</span></li>
      <li class="schedule__row"><span>Web. Bible Class</span><span class="schedule__leader"></span><span>7:00 Pm</span></li>
    </ul>
  </section>
</body>
</html>
```